"Velmora Crest" sexual performance enhancement pill bottle label needed.

This should be interesting...

I am starting a line of sexual performance enhancement products. This will be the first of several products basically. Keep in mind, I am the type of business person to stay with one company for years if they provide me with quality work.

This particular product is a male sexual performance pill. The name of the product is "Velmora Crest." The packaging of the pills are a black bottle with a white top. Label on the product example would be perfect but at a minimum I have attached a "template" for your guidance.

Some of the technical aspects of this are as follows:

-File Format: Illustrator CS6 is preferred. (Winner must provide artwork in layer and can not flatten artwork.)
-Resolution: 300 dpi minimum
-Bleed: 1/16th (0.0625") inch from edge of label
-Color Mode: CMYK only or must be converted to CMYK for final production

Lastly, this is your project as a designer, artist, creator, this is essentially a piece of you that will be sold and known by thousands of people. I have no color scheme that I prefer, just use the template and follow the layout. If you have any further questions, please feel free to contact me at any time.
Updates

Quick note on the product and what it does: -Powerful, long lasting, harder erections -Works in a minutes and last for hours -Enhances sexual desire and drive Thank you for your ideas...

Project Deadline Extended
Reason: We decided to extent the project for a few more days to let the last few concepts come in. So far things are looking really good and we definitely have seen some amazing designs. Thank you for your hard work and amazing creativity. Looking forward to seeing what we have come in the next couple of day. Very respectfully, Brev

ONLY THREE DAYS LEFT!!!! Please submit your ideas as soon as possible. And as always, thank you for your help!!! V/r, Brev

Industry/Entity Type

Graphic Design

```html
<!DOCTYPE html>
<html lang="en">
<head>
<meta charset="utf-8">
<title>Velmora Crest – Bottle Label</title>
<link rel="stylesheet" href="https://fonts.googleapis.com/css2?family=Oswald:wght@500;700&family=Roboto+Condensed:wght@400;700&display=swap">
<style>
  :root {
    --ink: #0d0d0d;
    --paper: #ffffff;
    --accent: #e3141f;
    --gold: #d9a21b;
    --stage: #d9d9d9;
    --rule: #1a1a1a;
  }
  * { box-sizing: border-box; margin: 0; padding: 0; }
  html, body { width: 1022px; height: 1200px; overflow: hidden; }
  body {
    background: var(--stage);
    font-family: "Roboto Condensed", Arial, sans-serif;
    position: relative;
  }
  .label {
    position: absolute;
    left: 31px; top: 410px;
    width: 960px; height: 381px;
    background: var(--paper);
    border-radius: 14px;
    overflow: hidden;
  }
  .panel-dark { position: absolute; top: 0; background: var(--ink); color: var(--paper); }
  .directions { left: 0; width: 391px; height: 228px; }
  .directions-copy {
    position: absolute; left: 30px; top: 46px; width: 290px;
    font-size: 8.2px; line-height: 1.3; text-align: justify;
  }
  .directions-copy p { margin-bottom: 7px; }
  .facts-panel { left: 692px; width: 268px; height: 228px; padding: 26px 18px 0 32px; }
  .base-band { position: absolute; left: 0; bottom: 0; width: 100%; height: 20px; background: var(--accent); }

  .disclaimer { position: absolute; left: 36px; top: 232px; width: 210px; font-size: 8.2px; line-height: 1.3; color: var(--ink); }
  .maker { position: absolute; left: 36px; top: 285px; font-size: 11px; line-height: 1.35; color: var(--ink); }

  .brand-name {
    position: absolute; left: 338px; top: 352px;
    transform: rotate(-90deg); transform-origin: left top;
    font-family: "Oswald", Arial, sans-serif; font-weight: 700;
    font-size: 46px; line-height: 1; letter-spacing: 0.5px;
    color: var(--accent); white-space: nowrap; text-transform: uppercase;
  }
  .claim {
    position: absolute; left: 391px; padding: 0 8px;
    font-family: "Oswald", Arial, sans-serif; font-weight: 500;
    color: var(--paper); white-space: nowrap; text-transform: uppercase;
  }
  .claim-desire { top: 39px; height: 23px; line-height: 23px; font-size: 13.5px; background: var(--accent); }
  .claim-performance { top: 65px; height: 24px; line-height: 24px; font-size: 14px; background: var(--ink); }
  .brand-mark { position: absolute; left: 427px; top: 98px; }
  .product-type { position: absolute; left: 397px; top: 234px; font-family: "Oswald", Arial, sans-serif; font-weight: 500; font-size: 13.5px; line-height: 1.05; color: var(--ink); text-transform: uppercase; }
  .guarantee-seal { position: absolute; left: 550px; top: 215px; }
  .count { position: absolute; left: 547px; top: 318px; font-family: "Oswald", Arial, sans-serif; font-weight: 700; font-size: 17px; color: var(--ink); }
  .count small { font-size: 10px; }

  .facts-title { font-family: "Roboto Condensed", Arial, sans-serif; font-weight: 700; font-size: 22px; line-height: 1.1; }
  .facts-serving { font-size: 11px; line-height: 1.3; margin-top: 4px; padding-bottom: 5px; border-bottom: 3px solid var(--paper); }
  .facts-head { display: flex; justify-content: space-between; font-size: 10px; padding: 4px 0 4px; border-bottom: 1px solid var(--paper); }
  .facts-row { display: flex; justify-content: space-between; font-size: 9.6px; margin-top: 5px; }
  .facts-blend { font-size: 9.6px; line-height: 1.33; text-align: justify; }
  .facts-foot { position: absolute; left: 724px; top: 248px; width: 218px; border-top: 1px solid var(--rule); padding-top: 5px; font-size: 11px; color: var(--ink); }
  .other-ingredients { position: absolute; left: 724px; top: 282px; width: 218px; font-size: 10px; line-height: 1.35; color: var(--ink); }
</style>
</head>
<body>
  <main class="label">
    <section class="panel-dark directions">
      <div class="directions-copy">
        <p>SUGGESTED USE: As a dietary supplement, take two (2) capsules 1 hour before physical activity, or as directed by your health care professional. Do not exceed two (2) capsules daily.</p>
        <p>CAUTION: Do not exceed recommended dose. This product is not intended for pregnant or nursing mothers, children under the age of 18, or individuals taking prescription drugs. Discontinue use immediately if nausea, sleeplessness, or nervousness occur. Do not take this product if you have a known medical condition including high blood pressure, diabetes, any cardiovascular disorder, heart disease, hyperthyroidism, or are taking anti-depressant medications. If you have questions about the advisability of taking this product, consult your physician prior to use.</p>
        <p>KEEP OUT OF THE REACH OF CHILDREN. DO NOT USE IF SAFETY SEAL IS DAMAGED OR MISSING. STORE AT ROOM TEMPERATURE.</p>
      </div>
    </section>
    <p class="disclaimer">* These statements have not been evaluated by the Food and Drug Administration. This product is not intended to diagnose, treat, cure or prevent any disease.</p>
    <p class="maker">Manufactured Exclusively For:<br>COMPANY INFO</p>

    <h1 class="brand-name">Velmora Crest</h1>
    <p class="claim claim-desire">Enhances sexual desire and drive</p>
    <p class="claim claim-performance">Powerful, long lasting, harder erections</p>
    <svg class="brand-mark" width="120" height="120" viewBox="0 0 120 120" aria-hidden="true">
      <circle cx="60" cy="60" r="52" fill="var(--accent)"/>
    </svg>
    <p class="product-type">Dietary<br>Supplement</p>
    <svg class="guarantee-seal" width="62" height="62" viewBox="0 0 62 62" role="img" aria-label="Guarantee seal">
      <circle cx="31" cy="31" r="30" fill="var(--gold)"/>
      <circle cx="31" cy="31" r="21" fill="var(--accent)"/>
    </svg>
    <p class="count">60 <small>TABLETS</small></p>

    <section class="panel-dark facts-panel">
      <h2 class="facts-title">Supplement Facts</h2>
      <p class="facts-serving">Serving Size: 2 Capsules<br>Servings Per Container: 30</p>
      <div class="facts-head"><span>Amount Per Serving</span><span>% Daily Value</span></div>
      <div class="facts-row"><span>VCX-Rx™ Proprietary Formula</span><span>1,560 mg &nbsp;†</span></div>
      <p class="facts-blend">Horny Goat Weed (herb powder), Maca (herb powder), Macuna Pruriens (L-Dopa), Polypodium Vulgare (herb powder), Yohimbe Bark (herb powder), Saw Palmetto (herb powder), Muira Puama (herb powder), Arginine (L-Arginine hydrochloride), Panax Ginseng (herb powder)</p>
    </section>
    <p class="facts-foot">† % Daily Value not established</p>
    <p class="other-ingredients">Other Ingredients: Gelatin, Magnesium Stearate, and Calcium Carbonate.</p>

    <div class="base-band"></div>
  </main>
</body>
</html>
```